Awesome photographers card for an awesome new business

Double sided business card Black background and silver logo in middle on one side. Details on otherside. please keep it simple

Industry/Entity Type

Photographer

Contact Information for Business Card

Gerald Fenwick
0452817360
GeraldFenwickPhotography47@mailbox.test
www.GeraldFenwickPhotography.test.au
Instagram _Gerald_fenwick

Requirements
Must have
• My logo in Silver
• please use instagram logo instead of "Instagram"

```html
<!DOCTYPE html>
<html lang="en">
<head>
<meta charset="utf-8">
<title>Gerald Fenwick Photography – Business Card</title>
<link href="https://fonts.googleapis.com/css2?family=Roboto:wght@300;400&family=Roboto+Condensed:wght@700&display=swap" rel="stylesheet">
<style>
  :root {
    --backdrop: #e9e6e1;
    --card-dark: #1a1b1d;
    --card-light: #f4f4f4;
    --silver: #b9b9b9;
    --ink: #555557;
    --ink-strong: #5b5b5d;
    --white: #ffffff;
  }
  * { margin: 0; padding: 0; box-sizing: border-box; }
  html, body {
    width: 1200px; height: 960px; overflow: hidden;
    background: var(--backdrop);
    font-family: "Roboto", Arial, sans-serif;
  }
  .canvas { position: relative; width: 1200px; height: 960px; }
  .card {
    position: absolute; left: 320px; width: 600px; height: 342px;
    border-radius: 18px;
  }
  .card--front { top: 108px; background: var(--card-dark); }
  .card--back { top: 493px; background: var(--card-light); }

  .front-mark {
    position: absolute; left: 0; right: 0; top: 140px;
    text-align: center; color: var(--silver);
    font-weight: 300; font-size: 50px; letter-spacing: 1px;
  }
  .front-web {
    position: absolute; left: 0; right: 0; top: 290px;
    text-align: center; color: var(--white);
    font-size: 14.5px; letter-spacing: 2.6px;
  }

  .badge { position: absolute; left: 408px; top: 34px; width: 160px; height: 160px; }
  .badge-ring { position: absolute; inset: 0; border: 3px solid var(--silver); border-radius: 50%; }
  .badge-name {
    position: absolute; inset: 0; display: flex; align-items: center; justify-content: center;
    text-align: center; color: var(--silver); font-size: 18px; font-weight: 400; line-height: 1.2;
  }

  .holder-name {
    position: absolute; left: 37px; top: 195px;
    font-family: "Roboto Condensed", Arial, sans-serif; font-weight: 700;
    font-size: 22px; color: var(--ink-strong); text-transform: uppercase;
  }
  .contact-list { position: absolute; left: 37px; top: 238px; list-style: none; }
  .contact-item {
    display: flex; align-items: center; height: 19px;
    font-size: 14.5px; color: var(--ink);
  }
  .contact-icon { width: 13px; height: 13px; margin-right: 12px; fill: var(--ink); flex: none; }
</style>
</head>
<body>
<main class="canvas">
  <section class="card card--front">
    <div class="front-mark">Gerald Fenwick</div>
    <div class="front-web">www.GeraldFenwickPhotography.test.au</div>
  </section>

  <section class="card card--back">
    <div class="badge">
      <div class="badge-ring"></div>
      <div class="badge-name">Gerald<br>Fenwick</div>
    </div>
    <h1 class="holder-name">Gerald Fenwick</h1>
    <ul class="contact-list">
      <li class="contact-item">
        <svg class="contact-icon" viewBox="0 0 16 16" aria-hidden="true"><path d="M3 1l3 0 1.5 4-2 1.3a9 9 0 0 0 4.2 4.2L11 8.5l4 1.5v3a2 2 0 0 1-2 2A13 13 0 0 1 1 3a2 2 0 0 1 2-2z"/></svg>
        0452817360
      </li>
      <li class="contact-item">
        <svg class="contact-icon" viewBox="0 0 16 16" aria-hidden="true"><path d="M1 3h14v10H1z M2 4l6 5 6-5" fill="none" stroke="#555557" stroke-width="1.6"/><path d="M1 3h14L8 8.5z"/></svg>
        GeraldFenwickPhotography47@mailbox.test
      </li>
      <li class="contact-item">
        <svg class="contact-icon" viewBox="0 0 16 16" aria-hidden="true"><circle cx="8" cy="8" r="6.5" fill="none" stroke="#555557" stroke-width="1.8"/><path d="M4 5l3 1 0 3-2 1zM9 4l3 2-1 3-2-1z"/></svg>
        www.GeraldFenwickPhotography.test.au
      </li>
      <li class="contact-item">
        <svg class="contact-icon" viewBox="0 0 16 16" aria-hidden="true"><rect x="1" y="1" width="14" height="14" rx="2"/></svg>
        Gerald_fenwick
      </li>
    </ul>
  </section>
</main>
</body>
</html>
```